Beacon Advisory Website

I currently have a website www.beaconadvisoryinc.com. We are a IT Consulting Company. Our website will pretty much tell out our services. I am looking to enhance my website and make it look more professional. Looking for very classy and Contemporary look and design for my website.

It Company

```html
<!DOCTYPE html>
<html lang="en">
<head>
<meta charset="utf-8">
<title>Beacon Advisory</title>
<link rel="stylesheet" href="https://fonts.googleapis.com/css2?family=Lato:wght@400;700&display=swap">
<style>
:root{
  --sky:#0099d8;
  --navy:#0b3f86;
  --navy-deep:#08306b;
  --ink:#333333;
  --text:#3a3a3a;
  --nav:#333333;
  --nav-line:#454545;
  --footer:#333333;
  --footer-top:#262626;
  --white:#ffffff;
  --muted:#9a9a9a;
}
*{box-sizing:border-box;margin:0;padding:0}
html,body{width:1147px;height:1200px;overflow:hidden}
body{position:relative;background:var(--white);font-family:'Lato',sans-serif;color:var(--text)}
.abs{position:absolute}

/* top bar */
.topbar{left:0;top:0;width:1147px;height:33px;background:var(--sky)}
.social-top{left:914px;top:0;display:flex;gap:1px}
.social-top span{width:34px;height:33px;background:var(--navy)}

/* header */
.brand{left:95px;top:50px;display:flex;align-items:center;gap:10px}
.brand-mark{width:40px;height:40px;border-radius:50%;background:var(--navy)}
.brand-name{font-weight:700;font-size:20px;letter-spacing:1px;color:var(--navy);line-height:1}
.phone{right:95px;top:63px;display:flex;align-items:center;gap:7px;font-size:17px;color:var(--ink);font-weight:700}

/* nav */
.nav{left:0;top:115px;width:1147px;height:41px;background:var(--nav)}
.nav ul{list-style:none;position:absolute;left:94px;top:0;display:flex;height:41px}
.nav li{display:flex;align-items:center;justify-content:center;color:var(--white);font-size:15px;font-weight:700;border-right:1px solid var(--nav-line);position:relative}
.nav li:last-child{border-right:0}
.nav li.active{background:var(--sky)}
.nav li.active::after{content:"";position:absolute;left:50%;bottom:0;margin-left:-6px;border:6px solid transparent;border-bottom-color:var(--white)}

/* hero */
.hero-photo{left:0;top:156px;width:1147px;height:450px;background:linear-gradient(100deg,#c9d2db 0%,#e9eef2 35%,#f3f4f5 55%,#b6c0cc 75%,#d9cfc4 100%)}
.hero-band{left:0;top:432px;width:1147px;height:174px;background:linear-gradient(180deg,rgba(12,62,136,.9),rgba(21,86,160,.82))}
.hero-title{left:0;top:450px;width:1147px;text-align:center;color:var(--white);font-size:29px;font-weight:700}
.hero-rule{left:246px;top:497px;width:655px;height:1px;background:rgba(255,255,255,.35)}
.hero-notch{left:565px;top:497px;border:8px solid transparent;border-top-color:var(--white)}
.hero-text{left:100px;top:516px;width:947px;text-align:center;color:var(--white);font-size:12px;font-weight:700;line-height:18.5px}
.hero-more{left:555px;top:586px;width:37px;height:20px;background:var(--white);border-radius:3px 3px 0 0;text-align:center;color:#666;font-size:20px;line-height:22px}

/* cards */
.card{top:650px;height:352px;background:var(--white);border-top:3px solid var(--navy);border-left:1px solid #e6e6e6;border-right:1px solid #e6e6e6;box-shadow:0 14px 14px -10px rgba(0,0,0,.12)}
.card-head{position:absolute;left:13px;top:15px;display:flex;align-items:center;gap:14px}
.card-icon{width:37px;height:37px;border-radius:50%;background:var(--ink);display:flex;align-items:center;justify-content:center}
.card-title{font-size:26px;font-weight:700;color:var(--ink);letter-spacing:-.3px}
.card-title b{color:var(--navy)}
.card-image{position:absolute;left:13px;top:66px;width:269px;height:118px;border:1px solid #d6d6d6}
.card-text{position:absolute;left:13px;width:272px;font-size:12.2px;line-height:17.2px;letter-spacing:.2px;color:var(--text)}
.card-plus{position:absolute;right:-1px;bottom:0;width:25px;height:25px;background:var(--navy);color:var(--white);font-size:22px;font-weight:700;text-align:center;line-height:24px}
.services{position:absolute;left:12px;top:310px;list-style:none;width:210px}
.services li{display:flex;align-items:center;gap:12px;height:32px;border-bottom:1px dotted #9a9a9a;font-size:13px;color:var(--ink)}
.services li:last-child{border-bottom:0}
.services svg{flex:none}

/* footer */
.footer{left:0;top:1057px;width:1147px;height:143px;background:var(--footer);border-top:3px solid var(--footer-top)}
.foot-links{left:96px;top:1089px;color:var(--white);font-size:14px;word-spacing:2px}
.foot-links i{font-style:normal;margin:0 5px;color:#ccc}
.newsletter{left:95px;top:1137px;display:flex;align-items:center}
.mail-ring{width:37px;height:37px;border-radius:50%;border:2px solid var(--white);background:var(--footer);display:flex;align-items:center;justify-content:center;position:relative;z-index:1}
.news-field{width:173px;height:37px;margin-left:-4px;background:var(--white);border-radius:0 3px 3px 0;font-size:12px;color:#777;padding-left:14px;line-height:37px}
.subscribe{margin-left:9px;width:98px;height:37px;background:var(--navy);color:var(--white);font-size:14px;font-weight:700;text-align:center;line-height:37px;border-radius:3px}
.foot-social{left:429px;top:1144px;display:flex;gap:9px}
.foot-social span{width:25px;height:25px;border-radius:50%;background:var(--white)}
.foot-brand{left:845px;top:1092px;display:flex;align-items:center;gap:9px}
.foot-brand .brand-mark{background:#7a7a7a;width:38px;height:38px}
.foot-brand .brand-name{color:#8e8e8e}
.copyright{right:98px;top:1162px;color:var(--white);font-size:12.5px}
</style>
</head>
<body>

<div class="abs topbar"></div>
<div class="abs social-top" aria-label="Social links"><span></span><span></span><span></span><span></span></div>

<div class="abs brand"><div class="brand-mark"></div><div class="brand-name">BEACON ADVISORY</div></div>
<div class="abs phone">
  <svg width="24" height="24" viewBox="0 0 24 24"><circle cx="12" cy="12" r="10.5" fill="none" stroke="#0b3f86" stroke-width="2"/><path d="M9 6.5c-1.5.6-2 2.2-1.2 4.3.9 2.4 2.8 4.7 4.9 5.9 1.4.8 2.8.6 3.5-.4l-1.8-1.9-1.3.6c-1.1-.6-2.2-2-2.6-3.2l1-1z" fill="#0b3f86"/></svg>
  555 014 2680
</div>

<nav class="abs nav">
  <ul>
    <li class="active" style="width:167px">COMPANY</li>
    <li style="width:157px">SERVICES</li>
    <li style="width:173px">SOLUTIONS</li>
    <li style="width:175px">RESOURCES</li>
    <li style="width:146px">CAREER</li>
    <li style="width:141px">CONTACT US</li>
  </ul>
</nav>

<div class="abs hero-photo" role="img" aria-label="Photo of smiling business colleagues meeting in a bright office"></div>
<div class="abs hero-band"></div>
<h1 class="abs hero-title">WELCOME TO BEACON ADVISORY</h1>
<div class="abs hero-rule"></div>
<div class="abs hero-notch"></div>
<p class="abs hero-text">Today's IT market is a dynamic, fast-paced industry, with ever-increasing demands. Meeting these demands for over 25 years, Beacon Advisory maintains a global presence, aggressively recruiting expertly qualified IT and Management Professionals from around the world and cultivating key partnerships with corporations to understand their business models end-to-end, with a goal of delivering exceptional client service and ensuring a consistent delivery of the talent needed to drive results.</p>
<div class="abs hero-more">+</div>

<section class="abs card" style="left:94px;width:296px">
  <div class="card-head">
    <div class="card-icon"><svg width="20" height="20" viewBox="0 0 20 20"><circle cx="10" cy="10" r="4" fill="#fff"/><g stroke="#fff" stroke-width="1.6"><path d="M10 1v3M10 16v3M1 10h3M16 10h3M3.6 3.6l2 2M14.4 14.4l2 2M3.6 16.4l2-2M14.4 5.6l2-2"/></g></svg></div>
    <h2 class="card-title"><b>IT</b> CONSULTING</h2>
  </div>
  <div class="card-image" role="img" aria-label="Photo of a woman working on a laptop in an office" style="background:linear-gradient(90deg,#cfd9e6,#eef2f4 60%,#d7e2d6)"></div>
  <p class="card-text" style="top:196px">Information technology should improve business results. Brightwell helps companies make sure it does. We look at IT issues strategically, in the broader context of our clients' business. Our experts provide an objective, independent perspective to help companies realize the full potential of their IT resources, investments and assets.</p>
  <div class="card-plus">+</div>
</section>

<section class="abs card" style="left:429px;width:296px">
  <div class="card-head">
    <div class="card-icon"><svg width="18" height="20" viewBox="0 0 18 20"><rect x="3" y="2" width="11" height="15" rx="1" fill="none" stroke="#fff" stroke-width="1.6"/><path d="M6 7h5M6 10h5M6 13h3" stroke="#fff" stroke-width="1.4"/><circle cx="13" cy="15" r="3.2" fill="#fff"/></svg></div>
    <h2 class="card-title"><b>WHAT</b> WE DO</h2>
  </div>
  <p class="card-text" style="top:70px">We are successful in deploying all students we trained into project with 2-3 weeks after training program. Our training programs will last for 6-8 weeks dependents on technology. We will provide on job support for trainees until technology comfort level is attained.</p>
  <ul class="services" style="top:174px">
    <li><svg width="20" height="20" viewBox="0 0 20 20"><circle cx="8" cy="12" r="4.5" fill="none" stroke="#0b3f86" stroke-width="2"/><circle cx="15" cy="5" r="3" fill="none" stroke="#0b3f86" stroke-width="1.8"/></svg>Technology</li>
    <li><svg width="20" height="20" viewBox="0 0 20 20"><circle cx="10" cy="4" r="2.5" fill="#0b3f86"/><rect x="7" y="8" width="6" height="11" fill="#0b3f86"/><rect x="1" y="9" width="3" height="10" fill="#0b3f86"/><rect x="16" y="9" width="3" height="10" fill="#0b3f86"/></svg>Offshore Business</li>
    <li><svg width="20" height="20" viewBox="0 0 20 20"><rect x="4" y="1" width="12" height="18" rx="2" fill="none" stroke="#0b3f86" stroke-width="1.8"/><circle cx="10" cy="10" r="3" fill="#0b3f86"/></svg>Application Developement</li>
    <li><svg width="20" height="20" viewBox="0 0 20 20"><g fill="none" stroke="#0b3f86" stroke-width="1.6"><circle cx="10" cy="5" r="3"/><circle cx="5" cy="13" r="3"/><circle cx="15" cy="13" r="3"/></g></svg>Enterprise Integration</li>
    <li><svg width="20" height="20" viewBox="0 0 20 20"><circle cx="10" cy="10" r="4" fill="none" stroke="#0b3f86" stroke-width="2"/><g stroke="#0b3f86" stroke-width="2"><path d="M10 1v4M10 15v4M1 10h4M15 10h4M3.6 3.6l2.8 2.8M13.6 13.6l2.8 2.8M3.6 16.4l2.8-2.8M13.6 6.4l2.8-2.8"/></g></svg>IT Consulting</li>
  </ul>
  <div class="card-plus">+</div>
</section>

<section class="abs card" style="left:759px;width:295px">
  <div class="card-head">
    <div class="card-icon"><svg width="20" height="20" viewBox="0 0 20 20"><circle cx="10" cy="10" r="4.5" fill="none" stroke="#fff" stroke-width="2"/><circle cx="10" cy="10" r="1.6" fill="#fff"/><g stroke="#fff" stroke-width="2.2"><path d="M10 1v3M10 16v3M1 10h3M16 10h3M3.6 3.6l2 2M14.4 14.4l2 2M3.6 16.4l2-2M14.4 5.6l2-2"/></g></svg></div>
    <h2 class="card-title"><b>OFF</b>SHORE</h2>
  </div>
  <div class="card-image" role="img" aria-label="Illustration of a blue world map with glowing connection lines" style="background:radial-gradient(circle at 60% 40%,#7cc8ef,#1f74b6 60%,#0d4a87)"></div>
  <p class="card-text" style="top:196px">Our Offshore development model has a unique distinction of providing efficient software solutions with cost and quality advantage, using state-of-the-art technologies, having the capacity to handle large projects and, above all, the ability to execute timely deliveries.</p>
  <div class="card-plus">+</div>
</section>

<footer class="abs footer"></footer>
<div class="abs foot-links">COMPANY<i>/</i>SERVICES<i>/</i>SOLUTIONS<i>/</i>RESOURCES<i>/</i>CAREER<i>/</i>CONTACT US</div>
<div class="abs newsletter">
  <div class="mail-ring"><svg width="18" height="13" viewBox="0 0 18 13"><rect x="1" y="1" width="16" height="11" fill="#fff"/><path d="M1 1l8 6 8-6" fill="none" stroke="#333" stroke-width="1.4"/></svg></div>
  <div class="news-field">Sign Up for Newsletter</div>
  <div class="subscribe">SUBSCRIBE</div>
</div>
<div class="abs foot-social" aria-label="Social links"><span></span><span></span><span></span><span></span></div>
<div class="abs foot-brand"><div class="brand-mark"></div><div class="brand-name">BEACON ADVISORY</div></div>
<div class="abs copyright">© 2016 BeaconAdvisory. All Right Reserved.</div>

</body>
</html>
```